Small Business Broker Business Card Design

A business card design for a small business brokerage, which is a financial service, not unlike real estate brokerage, but for small businesses such as laundromats, pizza shops, restaurants, cleaners etc. The designs should all be simple, more conservative in nature, using the colors and font of the logo. Again, think real estate Brokerage as a business context
Contact Information for Business Card
Name: Glen R. Harlow. Title: Small Business Advisor. Email: g.harlow@bayfieldcapitalworks.example. Mobile: (555) 274-3918. Office: (555) 806-2147. www.bayfieldcapitalworks.example

```html
<!DOCTYPE html>
<html lang="en">
<head>
<meta charset="utf-8">
<title>Bayfield Capital Works – Business Card</title>
<link rel="stylesheet" href="https://fonts.googleapis.com/css2?family=Montserrat:wght@400;500;600;700&display=swap">
<style>
  :root {
    --navy: #1c3a72;
    --navy-deep: #15305f;
    --green: #7cc242;
    --ink: #1f2530;
    --paper: #ffffff;
    --backdrop: #e9e7e4;
  }
  * { box-sizing: border-box; margin: 0; padding: 0; }
  html, body { width: 1200px; height: 786px; overflow: hidden; }
  body {
    background: var(--backdrop);
    font-family: "Montserrat", Arial, sans-serif;
    position: relative;
  }
  .card {
    position: absolute;
    top: 233px;
    width: 546px;
    height: 312px;
    border-radius: 4px;
    overflow: hidden;
    box-shadow: 0 8px 24px rgba(0,0,0,.18);
  }
  /* Front */
  .card-front { left: 42px; background: var(--paper); }
  .brand {
    position: absolute;
    top: 76px; left: 0; right: 0;
    text-align: center;
  }
  .brand-name {
    display: inline-flex; align-items: center; gap: 10px;
    font-weight: 700; font-size: 26px; letter-spacing: .5px;
    color: var(--navy); text-transform: uppercase;
  }
  .brand-mark { width: 16px; height: 16px; background: var(--navy); display: inline-block; }
  .divider {
    position: absolute; left: 220px; right: 40px; top: 186px;
    height: 1px; background: var(--green);
  }
  .person { position: absolute; left: 34px; top: 148px; }
  .person-name { font-weight: 700; font-size: 25px; line-height: 31px; color: var(--navy); }
  .person-title { font-size: 13px; color: var(--ink); margin-top: 1px; }
  .phones { position: absolute; left: 34px; top: 216px; list-style: none; }
  .phones li, .web li {
    display: flex; align-items: center; gap: 8px;
    font-size: 13px; color: var(--ink); line-height: 22px;
  }
  .phones svg, .web svg { width: 13px; height: 13px; fill: var(--navy); flex: none; }
  .web { position: absolute; right: 26px; top: 200px; list-style: none; }
  .web li { justify-content: flex-end; font-size: 12px; }
  .band-green {
    position: absolute; left: 0; bottom: 0; width: 290px; height: 14px;
    background: var(--green);
  }
  .band-navy {
    position: absolute; left: 290px; right: 0; bottom: 0; height: 44px;
    background: var(--navy);
  }
  /* Back */
  .card-back { left: 612px; background: var(--navy); }
  .back-texture {
    position: absolute; inset: 0;
    background: linear-gradient(200deg, #3a5b98 0%, var(--navy) 40%, var(--navy-deep) 100%);
  }
  .back-brand {
    position: absolute; left: 0; right: 0; top: 140px; text-align: center;
  }
  .back-brand .brand-name { color: var(--paper); font-size: 22px; }
  .back-brand .brand-mark { background: var(--paper); width: 14px; height: 14px; }
</style>
</head>
<body>
  <section class="card card-front">
    <div class="brand">
      <div class="brand-name"><span class="brand-mark"></span>Bayfield Capital Works, Inc</div>
    </div>
    <div class="person">
      <div class="person-name">Glen R. Harlow</div>
      <div class="person-title">Small Business Advisor</div>
    </div>
    <div class="divider"></div>
    <ul class="phones">
      <li><svg viewBox="0 0 16 16"><path d="M2 6c0-2 3-3 6-3s6 1 6 3v1h-3V6H5v1H2zM4 8h8l1 5H3z"/></svg>(555) 806-2147</li>
      <li><svg viewBox="0 0 16 16"><path d="M4 1l3 3-2 2c1 2 3 4 5 5l2-2 3 3-2 3C7 15 1 9 1 3z"/></svg>(555) 274-3918</li>
    </ul>
    <ul class="web">
      <li>g.harlow@bayfieldcapitalworks.example<svg viewBox="0 0 16 16"><path d="M1 3h14v10H1zM2 4l6 5 6-5z" fill-rule="evenodd"/></svg></li>
      <li>www.bayfieldcapitalworks.example<svg viewBox="0 0 16 16"><circle cx="8" cy="8" r="7"/></svg></li>
    </ul>
    <div class="band-green"></div>
    <div class="band-navy"></div>
  </section>

  <section class="card card-back">
    <div class="back-texture" role="img" aria-label="Subtle tone-on-tone pattern across the navy card back"></div>
    <div class="back-brand">
      <div class="brand-name"><span class="brand-mark"></span>Bayfield Capital Works, Inc</div>
    </div>
  </section>
</body>
</html>
```